Redesign of an existing homepage

This site needs a redesign
https://www.wanderhof-kelbach.de
This page with the accommodation options is important for the customer
https://www.wanderhof-kelbach.de/gastgeber/
Till now there is a new logo. See attachment. That's all I have.
It would make sense to use the colors of the logo in the redesign.
footer.jpg.
I would put this info into the footer. The graphic (Infomaterial) is not needed.
a new menu - links.jpg
This info can be put in a new menu. Therefore the right column is gone and there is more space for the design.
NEW:
Please keep in mind that the Icons are important and shall be displayed under every accommodation

```html
<!DOCTYPE html>
<html lang="de">
<head>
<meta charset="utf-8">
<title>Wanderverband Kelbach – Startseite</title>
<link rel="stylesheet" href="https://fonts.googleapis.com/css2?family=Poppins:wght@400;500;600;700;800&display=swap">
<style>
:root{
  --blue:#0b6bb4;
  --blue-light:#5aa6dc;
  --green:#7ab51d;
  --green-soft:#e4f2dc;
  --ink:#161616;
  --text:#2b2b2b;
  --muted:#8a8a8a;
  --band:#eef6fc;
  --white:#fff;
}
*{margin:0;padding:0;box-sizing:border-box}
html,body{width:1200px;height:3552px;overflow:hidden}
body{position:relative;font-family:"Poppins",sans-serif;color:var(--text);background:var(--white)}
.abs{position:absolute}
.btn{position:absolute;display:flex;align-items:center;justify-content:center;background:var(--blue);color:var(--white);border-radius:22px;font-size:14px;font-weight:500;text-decoration:none}
.accent{color:var(--blue)}

/* hero */
.hero-bg{left:0;top:0;width:1200px;height:600px;background:radial-gradient(ellipse at 10% 20%,#eaf3fb 0%,#ffffff 60%)}
.hero-art{left:0;top:0;width:1200px;height:520px}
.topnav{left:124px;top:22px;width:952px;height:77px;background:var(--white);border-radius:40px;box-shadow:0 6px 24px rgba(0,0,0,.06);display:flex;align-items:center;padding:0 0 0 34px}
.brand{display:flex;align-items:center;gap:8px;font-size:11px;font-weight:700;color:var(--blue);line-height:1.15;width:200px}
.brand-dot{width:26px;height:26px;border-radius:50%;background:var(--green)}
.menu{display:flex;gap:29px;margin-left:97px;font-size:13px;font-weight:500;color:var(--ink)}
.menu-cta{position:absolute;right:20px;top:17px;width:93px;height:42px;border-radius:21px;background:var(--blue);color:#fff;font-size:13px;font-weight:500;display:flex;align-items:center;justify-content:center}
.hero-title{left:142px;top:230px;width:440px;font-size:36px;font-weight:700;line-height:46px;color:var(--ink);text-transform:uppercase;letter-spacing:.2px}

/* about */
.about-panel{left:142px;top:703px;width:306px;height:425px;background:var(--green-soft);border-radius:14px}
.about-photo{left:161px;top:656px;width:301px;height:454px;border-radius:14px;background:linear-gradient(170deg,#b9cfa0 0%,#8a9a5c 45%,#a57a4e 100%)}
.about-title{left:542px;top:661px;width:520px;font-size:30px;font-weight:600;line-height:40px;color:var(--ink)}
.about-copy{left:542px;top:757px;width:510px;font-size:13.5px;line-height:23px;color:var(--text)}
.about-copy p{margin-bottom:7px}

/* hosts */
.hosts{left:0;top:1214px;width:1200px;height:489px;background:var(--band)}
.section-title{position:absolute;left:0;width:1200px;text-align:center;font-size:30px;font-weight:600;color:var(--ink)}
.host-card{position:absolute;top:1358px;width:291px;height:206px}
.host-photo{width:291px;height:173px;border-radius:14px}
.host-info{position:absolute;left:21px;top:131px;width:248px;height:75px;background:var(--blue-light);border-radius:8px;color:#fff;padding:11px 14px}
.host-info h3{font-size:13px;font-weight:600;margin-bottom:3px}
.host-info p{font-size:10px;line-height:14px}
.host-go{position:absolute;right:12px;top:24px;width:28px;height:28px;border-radius:50%;background:#fff}

/* reviews */
.review{position:absolute;top:1882px;width:517px;height:287px;border-radius:16px;text-align:center}
.review.is-active{background:#fff;box-shadow:0 8px 40px rgba(20,60,110,.08)}
.avatar{position:absolute;left:227px;top:30px;width:63px;height:63px;border-radius:50%;background:linear-gradient(135deg,#c8a98c,#6d5646)}
.quote-mark{position:absolute;left:42px;top:40px;font-size:130px;line-height:1;color:#e8edf2;font-family:Georgia,serif}
.stars{position:absolute;left:0;top:108px;width:517px;color:#f6a623;font-size:17px;letter-spacing:3px}
.review h4{position:absolute;left:0;top:136px;width:517px;font-size:15px;font-weight:600;color:var(--ink)}
.review p{position:absolute;left:30px;top:194px;width:457px;font-size:13px;line-height:23px;color:var(--text)}
.pager-prev{left:574px;top:2225px;font-size:18px;color:var(--green)}
.pager-next{left:601px;top:2216px;width:36px;height:36px;border-radius:50%;background:var(--green)}

/* reach */
.reach{left:142px;top:2337px;width:916px;height:245px;border-radius:14px;background:linear-gradient(180deg,#e3eefb 0%,#eef7ec 100%)}
.reach-link{left:0;top:2478px;width:1200px;text-align:center;font-size:13px;font-weight:600;color:var(--ink);text-decoration:underline}

/* contact */
.map{left:0;top:2655px;width:712px;height:458px;background:linear-gradient(135deg,#d9f3e3 0%,#cfeedd 50%,#e5f4d9 100%)}
.contact{left:712px;top:2655px;width:488px;height:458px;background:var(--green);color:#fff}
.contact h2{position:absolute;left:63px;top:64px;font-size:32px;font-weight:600}
.contact-row{position:absolute;left:80px;display:flex;align-items:flex-start;gap:16px;font-size:12.5px;font-weight:500;line-height:19px}
.contact-row svg{flex:none}
.contact-rule{position:absolute;left:63px;top:345px;width:362px;height:1px;background:rgba(255,255,255,.35)}

/* footer */
.footer-fog{left:0;top:3300px;width:1200px;height:252px;background:linear-gradient(180deg,#ffffff 0%,#e8ecec 30%,#7d8a80 75%,#3d4a3f 100%)}
.footer-rider{left:1020px;top:3240px;width:180px;height:312px;background:linear-gradient(180deg,rgba(255,255,255,0) 0%,rgba(96,110,120,.5) 60%,rgba(50,60,55,.7) 100%)}
.footer-brand{left:0;top:3205px;width:1200px;display:flex;flex-direction:column;align-items:center;gap:10px}
.footer-brand .mark{width:72px;height:72px;border-radius:50%;background:var(--green)}
.footer-brand span{font-size:20px;font-weight:700;color:var(--blue);letter-spacing:.3px}
.footer-nav{left:142px;top:3364px;width:916px;display:flex;justify-content:space-between;font-size:12px;color:var(--ink)}
.footer-nav .current{color:var(--blue)}
.legal{left:142px;top:3506px;font-size:11px;color:#fff}
.social{left:914px;top:3497px;display:flex;gap:5px}
.social i{display:block;width:33px;height:33px;border-radius:50%;background:var(--green)}
</style>
</head>
<body>

<div class="abs hero-bg"></div>
<svg class="abs hero-art" viewBox="0 0 1200 520" aria-hidden="false">
  <path d="M1200,330 L1200,360 C1150,410 1110,430 1080,432 Z" fill="#e4f2dc"/>
  <path d="M1200,300 L1200,330 L1080,425 Z" fill="var(--blue)"/>
  <path d="M585,0 L1200,0 L1200,290 C1120,350 1000,505 860,503 C720,501 600,430 560,310 C530,200 545,80 585,0 Z" fill="#d8eaf8"/>
  <path role="img" aria-label="Foto: Familie mit zwei Kindern beim Herbstspaziergang" d="M600,0 L1200,0 L1200,295 C1120,355 1000,500 860,498 C725,496 610,425 575,305 C548,195 562,70 600,0 Z" fill="url(#heroTone)"/>
  <defs>
    <linearGradient id="heroTone" x1="0" y1="0" x2="1" y2="1">
      <stop offset="0" stop-color="#c9a878"/>
      <stop offset=".5" stop-color="#8c7a5a"/>
      <stop offset="1" stop-color="#5d6a4a"/>
    </linearGradient>
  </defs>
</svg>

<nav class="abs topnav">
  <div class="brand"><span class="brand-dot"></span><span>WANDERVERBAND<br>KELBACH</span></div>
  <div class="menu"><span>Kelbach</span><span>Rottal-Inn</span><span>Thermenland</span><span>Wanderverband</span><span>Ostbayern</span></div>
  <a class="menu-cta">Kontakt</a>
</nav>

<h1 class="abs hero-title">Fremdenverkehrsver<br>ein Kelbach und<br>Umgebung</h1>
<a class="btn" style="left:142px;top:403px;width:129px;height:41px">Mehr Erfahren</a>

<!-- about -->
<div class="abs about-panel"></div>
<div class="abs about-photo" role="img" aria-label="Foto: Familie mit Kind wandert auf einem Feldweg unter Kiefern"></div>
<h2 class="abs about-title"><span class="accent">Urlaub Im Rottal</span> - Dem Schönsten Fleck Bayerns</h2>
<div class="abs about-copy">
  <p>Lieber Besucherinnen und Besucher,</p>
  <p>Kelbach und Umgebung haben all das, was das Leben lebenswert macht: Kultur und Natur, Lebensfreude und Genuss, freundliche und aufgeschlossene Menschen…</p>
  <p>Ob Kirchen, Brunnen oder andere Baudenkmäler – bei einem Rundgang durch die Rottaler Ross-Stadt kann man viele liebevolle Details für sich entdecken.</p>
  <p>Für Bewegungsfreudige und Erholungssuchende gibt es “Natur pur” in und um Kelbach! Hier kann man sportlich unterwegs sein beim Radeln, Walken, Wandern, Golfen, Reiten und Baden oder einfach nur die Ruhe genießen.</p>
  <p>Freizeit und Erholung für die ganze Familie – planen Sie einen Urlaub auf dem Bauernhof, in einer Ferienwohnung oder im Hotel. Ihr Urlaub im Rottal wird ein einmaliges Erlebnis!</p>
</div>
<a class="btn" style="left:542px;top:1081px;width:130px;height:41px">Mehr Erfahren</a>

<!-- hosts -->
<section class="abs hosts"></section>
<h2 class="section-title" style="top:1282px">Gastgeber Im <span class="accent">Rottal</span></h2>

<article class="host-card" style="left:142px">
  <div class="host-photo" role="img" aria-label="Foto: Luftbild eines Campingplatzes in hügeliger Landschaft" style="background:linear-gradient(180deg,#cfe0ef 0%,#b5c7a2 45%,#8fa67a 100%)"></div>
  <div class="host-info"><h3>Wiesencamp Lindenau</h3><p>Lindenweg 7, 94199 Lindenau<br>Wohneinheiten</p><span class="host-go"></span></div>
</article>
<article class="host-card" style="left:454px">
  <div class="host-photo" role="img" aria-label="Foto: Holzhaus mit Blumenbalkon im Grünen" style="background:linear-gradient(180deg,#9ab8d6 0%,#4a3b2c 45%,#5f8a3a 100%)"></div>
  <div class="host-info"><h3>Brunnerhäusl</h3><p>Feldstraße 3, 84398 Moosried<br>1 Wohneinheit</p><span class="host-go"></span></div>
</article>
<article class="host-card" style="left:767px">
  <div class="host-photo" role="img" aria-label="Foto: Landhaus mit Balkon zwischen Bäumen" style="background:linear-gradient(180deg,#e6ecef 0%,#8a7a6c 40%,#6f9a58 100%)"></div>
  <div class="host-info"><h3>Landhaus Haslinger</h3><p>Lindenweg 11, 94199 Lindenau<br>Wohneinheiten</p><span class="host-go"></span></div>
</article>
<svg class="abs" style="left:0;top:0;width:1200px;height:1600px;pointer-events:none" viewBox="0 0 1200 1600" aria-hidden="true">
  <g stroke="var(--blue-light)" stroke-width="1.6" fill="none" stroke-linecap="round">
    <path d="M379,1532 l8,-8 m-6,0 h6 v6"/>
    <path d="M691,1532 l8,-8 m-6,0 h6 v6"/>
    <path d="M1004,1532 l8,-8 m-6,0 h6 v6"/>
  </g>
</svg>
<a class="btn" style="left:542px;top:1600px;width:115px;height:40px">Damit Mehr</a>

<!-- reviews -->
<h2 class="section-title" style="top:1797px">Was Unsere Kunden Über <span class="accent">Uns Sagen</span></h2>

<article class="review" style="left:-205px">
  <span class="quote-mark">“</span><span class="avatar" role="img" aria-label="Porträtfoto Tom Reiber"></span>
  <div class="stars">★★★★★</div><h4>Tom Reiber</h4>
  <p>There are many variations of passages of Lorem Ipsum available, but the majority have suffered alteration in some form, by injected humour, or randomised words which don't look even slightly believable.</p>
</article>
<article class="review is-active" style="left:341px">
  <span class="quote-mark">“</span><span class="avatar" role="img" aria-label="Porträtfoto Markus Feldner"></span>
  <div class="stars">★★★★★</div><h4>Markus Feldner</h4>
  <p>There are many variations of passages of Lorem Ipsum available, but the majority have suffered alteration in some form, by injected humour, or randomised words which don't look even slightly believable.</p>
</article>
<article class="review" style="left:887px">
  <span class="quote-mark">“</span><span class="avatar" role="img" aria-label="Porträtfoto Jonas Albrecht"></span>
  <div class="stars">★★★★★</div><h4>Jonas Albrecht</h4>
  <p>There are many variations of passages of Lorem Ipsum available, but the majority have suffered alteration in some form, by injected humour, or randomised words which don't look even slightly believable.</p>
</article>
<span class="abs pager-prev">‹</span>
<svg class="abs pager-next" viewBox="0 0 36 36" aria-hidden="true"><path d="M15,12 l6,6 l-6,6" stroke="#fff" stroke-width="2" fill="none" stroke-linecap="round"/></svg>

<!-- reach -->
<div class="abs reach"></div>
<h2 class="section-title" style="top:2421px">So Erreichen <span class="accent">Sie Uns</span></h2>
<a class="abs reach-link">Bitte akzeptieren Sie das Cookie "Externe Medien", um die Karte anzuzeigen</a>

<!-- contact -->
<div class="abs map" role="img" aria-label="Karte der Region mit Standorten der Gastgeber"></div>
<section class="abs contact">
  <h2>Kontakt aufnehmen</h2>
  <div class="contact-row" style="top:126px">
    <svg width="30" height="32" viewBox="0 0 30 32" fill="none" stroke="#fff" stroke-width="1.6"><path d="M15,29 C8,20 6,16 6,12 a9,9 0 0 1 18,0 c0,4 -2,8 -9,17 Z"/><circle cx="15" cy="12" r="3.5"/><path d="M6,29 h18"/></svg>
    <div>Marktgasse 4<br>84399 Kelbach</div>
  </div>
  <div class="contact-row" style="top:180px">
    <svg width="30" height="32" viewBox="0 0 30 32" fill="none" stroke="#fff" stroke-width="1.6"><path d="M8,5 l5,6 -3,3 c2,4 5,7 9,9 l3,-3 6,5 -3,4 C14,28 4,18 4,9 Z"/><path d="M18,5 a8,8 0 0 1 8,8 M18,9 a4,4 0 0 1 4,4"/></svg>
    <div>Telefon<br>08577 / 412 3300</div>
  </div>
  <div class="contact-row" style="top:234px">
    <svg width="30" height="32" viewBox="0 0 30 32" fill="none" stroke="#fff" stroke-width="1.6"><rect x="4" y="10" width="22" height="18" rx="2"/><rect x="9" y="3" width="12" height="9"/><path d="M9,16 h4 M9,20 h4 M9,24 h4 M17,16 h4 M17,20 h4 M17,24 h4"/></svg>
    <div>Telefax<br>08577 / 412 3309</div>
  </div>
  <div class="contact-row" style="top:288px">
    <svg width="30" height="32" viewBox="0 0 30 32" fill="none" stroke="#fff" stroke-width="1.6"><path d="M3,13 l12,-9 12,9 v15 H3 Z"/><path d="M3,13 l12,9 12,-9"/><path d="M8,10 h14 M8,14 h14"/></svg>
    <div>E-mail<br>info@wanderhof-kelbach.de</div>
  </div>
  <div class="contact-rule"></div>
  <div class="contact-row" style="top:368px">
    <svg width="30" height="32" viewBox="0 0 30 32" fill="none" stroke="#fff" stroke-width="1.6"><circle cx="15" cy="16" r="12"/><circle cx="15" cy="16" r="9"/><path d="M15,10 v6 l4,3"/></svg>
    <div>Mo-Do&nbsp; 9:00 - 16:00 Uhr<br>Fr&nbsp; 9:00 - 12:30 Uhr</div>
  </div>
</section>

<!-- footer -->
<div class="abs footer-fog" role="img" aria-label="Foto: Nebliger Waldrand in der Abenddämmerung"></div>
<div class="abs footer-rider" role="img" aria-label="Foto: Mountainbiker auf einem Hügel"></div>
<div class="abs footer-brand"><span class="mark"></span><span>WANDERVERBAND KELBACH</span></div>
<nav class="abs footer-nav">
  <span class="current">Startseite</span><span>Gastgeber</span><span>Rottal</span><span>Freizeit</span><span>Ausflugsziele</span><span>Kunst und Kultur</span><span>Veranstaltungen</span><span>Kontakt</span>
</nav>
<p class="abs legal">© 2025 WANDERVERBAND KELBACH. All Rights Reserved. &nbsp; I &nbsp; Information material &nbsp; I &nbsp; imprint &nbsp; I &nbsp; Data protection</p>
<div class="abs social"><i></i><i></i><i></i><i></i></div>

</body>
</html>
```